Commercial Cleaning Company Website Design

We are working with Harbor Tidy Team. They are a commercial cleaning company that needs a new website design.

Some sites to use for inspiration:

https://www.plenvask.com
https://gleam-panecare.com
https://tidwellhelpers.net
https://quietnesthouse.com
https://www.thedustingbureau.com
https://www.pennytidy.com

Thank you for taking the time to consider designing a website for us. We are web developers based in Stockton and Los Angeles, CA, USA. Most of our projects go through the same process. Understanding this process may help you win a project with us. We custom-code all of our websites in-house. We don’t have any requirements as to what tools you use for your design, but we prefer Figma files. For any design that we label as four-stars, we send it to the client for review. The client picks the final design they want us to use. Once we complete this process, we will continue to show additional clients all the four-star sites and purchase them later. Your designs will have multiple chances to sell. For better chances of success, we ask that you follow these guidelines.

IMAGES:
If you use any images or icons in the design, we ask that you have a link to the asset so we can purchase the image/icon. Most of the designs we submit do not have the customer’s images on them unless they have some great images. Be creative; show us the feeling you are trying to portray with your image choices. Use any royalty-free site you choose. We subscribe to Adobe and mainly use their images, but we can purchase images outside of Adobe.

PLEASE NOTE: we will not submit designs to clients with watermarks on the images.

FONTS:
We ask that you identify the fonts used in the design. This can be done in a message if you want. We typically use Google Fonts and Adobe Fonts.

CONTENT:
We're always open to different content and ideas. We often submit designs with stock images so the client can see our vision. We typically take pictures after the website launch to use their images with our vision. Lorem Ipsum is fine for paragraphs, but we ask that you write the headers in correct English. We want to be able to show the vision and identify the sections of the website.

INSPIRATION:
We typically add a couple of links in the brief of websites we like to help you get started in your design.

REVISIONS:
We do not often ask for revisions of the designs unless we see something in the design that may not appeal to the client. If there are slight changes that we want to make, we do that in the development process.

FEEDBACK:
We rarely give feedback on designs during the design process. We are working on many website projects and do not have the time to provide feedback. We usually respond if your request is well thought out and asks specific questions, but a note asking “feedback, please” usually goes unanswered.

```html
<!DOCTYPE html>
<html lang="en">
<head>
<meta charset="utf-8">
<title>Harbor Tidy Team – Commercial Cleaning</title>
<link href="https://fonts.googleapis.com/css2?family=Poppins:wght@400;500;600;700;800&family=Open+Sans:wght@400;600&display=swap" rel="stylesheet">
<style>
:root{
  --orange:#f7a21b;
  --orange-deep:#f08a00;
  --yellow:#fdc12a;
  --red:#e2251b;
  --navy:#1c3f94;
  --ink:#1d1d1f;
  --body:#5b5b63;
  --mist:#eef2fa;
  --footer:#0d0d0f;
  --white:#ffffff;
}
*{box-sizing:border-box;margin:0;padding:0}
html,body{width:1200px;height:4124px;overflow:hidden;background:var(--white)}
body{position:relative;font-family:"Open Sans",Arial,sans-serif;color:var(--body)}
.abs{position:absolute}
h1,h2,h3,h4,.brand,.nav,.btn{font-family:"Poppins",Arial,sans-serif}
p{font-size:15px;line-height:25px}
.btn{display:inline-block;background:var(--red);color:var(--white);font-weight:600;font-size:14px;text-transform:uppercase;padding:12px 28px;border-radius:24px;letter-spacing:.3px}
.section-title{font-weight:700;color:var(--navy);font-size:30px;text-transform:uppercase;letter-spacing:.5px}
.title-bar{display:block;width:60px;height:4px;background:var(--navy);margin-top:10px;border-radius:2px}
.centered{left:0;width:1200px;text-align:center}
.centered .title-bar{margin:12px auto 0}

/* header */
.header{top:0;left:0;width:1200px;height:120px;background:var(--white);z-index:5}
.brand{left:40px;top:34px;display:flex;align-items:center;gap:14px;font-weight:800;font-size:26px;color:var(--navy);text-transform:uppercase;letter-spacing:1px}
.brand-dot{width:40px;height:40px;border-radius:50%;background:var(--orange)}
.topbar{left:660px;top:0;width:540px;height:48px;background:var(--orange);border-bottom-left-radius:24px;display:flex;align-items:center;justify-content:space-around;color:var(--white);font-size:14px;font-weight:600}
.topbar span{display:flex;align-items:center;gap:8px}
.nav{left:460px;top:60px;width:720px;display:flex;justify-content:space-around;font-size:15px;font-weight:600;color:var(--navy);text-transform:uppercase}
.nav a{padding:10px 4px;color:inherit;text-decoration:none}
.nav .active{border-bottom:3px solid var(--navy)}

/* hero */
.hero{top:120px;left:0;width:1200px;height:560px;background:linear-gradient(100deg,#3a3e44 0%,#6f7379 45%,#a9adb2 75%,#cfd2d4 100%)}
.hero-shade{top:120px;left:0;width:1200px;height:560px;background:linear-gradient(90deg,rgba(10,14,24,.72) 0%,rgba(10,14,24,.35) 45%,rgba(10,14,24,0) 70%)}
.hero-copy{left:108px;top:188px;width:620px;color:var(--white)}
.hero-copy h1{font-size:38px;line-height:48px;font-weight:800;text-transform:uppercase}
.hero-copy .tagline{font-family:"Poppins",Arial,sans-serif;font-size:18px;font-weight:600;margin:14px 0 22px}
.hero-wave{top:560px;left:0}

/* about */
.about-photo-main{left:112px;top:896px;width:370px;height:250px;background:linear-gradient(135deg,#c9d6e2,#8ea4b8 60%,#5d6c7a)}
.about-photo-small{left:360px;top:950px;width:232px;height:240px;background:linear-gradient(160deg,#d8d2c6,#9a9385 60%,#5c574f);border:6px solid var(--white)}
.about-copy{left:640px;top:880px;width:520px}
.about-copy p{margin-top:22px}

/* services */
.services{top:1288px;left:0;width:1200px;height:572px;background:linear-gradient(180deg,var(--yellow) 0%,var(--orange) 60%,var(--orange-deep) 100%)}
.services .section-title{color:var(--white)}
.services .title-bar{background:var(--white)}
.service-card{top:1448px;width:296px;height:312px;background:var(--white);border-radius:18px;padding:12px;text-align:center;box-shadow:0 8px 20px rgba(120,60,0,.18)}
.service-photo{width:272px;height:196px;border-radius:12px}
.service-icon{width:62px;height:62px;border-radius:50%;background:var(--white);border:3px solid var(--orange);margin:-34px auto 0;position:relative;display:flex;align-items:center;justify-content:center}
.service-card h3{font-size:14px;font-weight:700;color:var(--ink);text-transform:uppercase;margin-top:16px}

/* why */
.feature{width:280px}
.feature h4{font-size:16px;font-weight:700;color:var(--ink);text-transform:uppercase;margin-bottom:8px}
.feature p{font-size:14px;line-height:22px}
.why-frame{left:440px;top:2050px;width:320px;height:430px;border:4px solid var(--orange);border-radius:40px}
.why-emblem{left:530px;top:2175px;width:140px;height:140px;border-radius:50%;background:linear-gradient(180deg,var(--yellow),var(--red))}
.corner-icon{width:62px;height:62px;border-radius:50%;background:var(--orange);display:flex;align-items:center;justify-content:center}

/* commercial */
.commercial{top:2540px;left:0;width:1200px;height:580px;background:var(--mist)}
.commercial-copy{left:112px;top:2630px;width:440px}
.commercial-copy h2{line-height:40px}
.commercial-copy .stat{font-family:"Poppins",Arial,sans-serif;font-size:17px;font-weight:600;color:var(--ink);margin:30px 0 10px}
.commercial-copy p+p{margin-top:18px}
.tile{border-radius:6px}
.collage-center{left:800px;top:2780px;width:96px;height:96px;border-radius:50%;background:var(--white);border:5px solid var(--orange)}

/* partners */
.partners-copy{left:120px;top:3300px;width:960px;text-align:center;font-size:15px}
.partner{top:3400px;width:96px;height:96px;border-radius:50%}

/* footer */
.footer{top:3680px;left:0;width:1200px;height:444px;background:var(--footer);color:#d6d6d6}
.footer-wave{top:3560px;left:0}
.footer-brand{left:112px;top:3790px;display:flex;align-items:center;gap:12px;font-family:"Poppins",Arial,sans-serif;font-weight:800;font-size:24px;color:var(--white);text-transform:uppercase;letter-spacing:1px}
.socials{left:112px;top:3880px;display:flex;gap:12px}
.socials span{width:34px;height:34px;border-radius:50%;background:var(--orange)}
.footer-col{top:3780px;color:#d6d6d6}
.footer-col h4{font-size:20px;font-weight:700;color:var(--white);margin-bottom:18px}
.footer-col li{list-style:none;font-size:14px;line-height:30px;display:flex;align-items:center;gap:10px}
.footer-col li::before{content:"";width:8px;height:8px;background:var(--orange);transform:rotate(45deg)}
.contact-row{display:flex;align-items:center;gap:14px;font-size:14px;margin-bottom:22px}
.contact-icon{width:34px;height:34px;border-radius:50%;background:var(--orange);display:flex;align-items:center;justify-content:center;flex:none}
.copyright{left:0;top:4060px;width:1200px;border-top:1px solid #2b2b30;padding-top:20px;text-align:center;font-size:14px;color:#bdbdbd}
</style>
</head>
<body>

<!-- Header -->
<header class="abs header">
  <div class="abs brand"><span class="brand-dot"></span>Harbor Tidy Team</div>
  <div class="abs topbar">
    <span><svg width="18" height="14" viewBox="0 0 18 14"><rect x="1" y="1" width="16" height="12" rx="2" fill="none" stroke="#fff" stroke-width="2"/><path d="M1 2l8 6 8-6" fill="none" stroke="#fff" stroke-width="2"/></svg>EMAIL: info@harbortidyteam.com</span>
    <span><svg width="16" height="16" viewBox="0 0 24 24"><path d="M6 2h4l2 5-3 2a12 12 0 006 6l2-3 5 2v4a2 2 0 01-2 2A18 18 0 014 4a2 2 0 012-2z" fill="#fff"/></svg>PHONE: +555 5555 5555</span>
  </div>
  <nav class="abs nav">
    <a class="active">Home</a><a>About Us</a><a>Services</a><a>Testimonials</a><a>Contact Us</a>
  </nav>
</header>

<!-- Hero -->
<section>
  <div class="abs hero" role="img" aria-label="Photo of a cleaner using a floor scrubbing machine in a bright modern office"></div>
  <div class="abs hero-shade"></div>
  <div class="abs hero-copy">
    <h1>Professional Commercial Cleaning for Office &amp; Facility Spaces</h1>
    <div class="tagline">Reliable - Certified - Eco-Friendly</div>
    <span class="btn">Request a Free Quote</span>
  </div>
  <svg class="abs hero-wave" width="1200" height="160" viewBox="0 0 1200 160">
    <path d="M0 40 C260 130 460 10 600 70 C760 140 960 20 1200 30 L1200 160 L0 160Z" fill="var(--orange)"/>
    <path d="M0 64 C260 150 460 36 600 92 C760 160 960 46 1200 56 L1200 160 L0 160Z" fill="#fff"/>
    <circle cx="600" cy="124" r="26" fill="#fff" stroke="var(--orange)" stroke-width="3"/>
    <circle cx="600" cy="124" r="13" fill="var(--red)"/>
  </svg>
</section>

<!-- About -->
<section>
  <div class="abs about-photo-main" role="img" aria-label="Photo of a floor polishing machine in a glass-walled office"></div>
  <div class="abs about-photo-small" role="img" aria-label="Photo of cleaners wiping desks in a workspace"></div>
  <div class="abs about-copy">
    <h2 class="section-title">Who We Are<span class="title-bar"></span></h2>
    <p>Lorem ipsum dolor sit amet, consectetur adipiscing elit, sed do eiusmod tempor incididunt ut labore et dolore magna aliqua. Ut enim ad minim veniam, quis nostrud exercitation ullamco laboris nisi ut aliquip ex ea commodo consequat.</p>
    <p>Duis aute irure dolor in reprehenderit in voluptate velit esse cillum dolore eu fugiat nulla pariatur. Excepteur sint occaecat cupidatat non proident, sunt in culpa qui officia deserunt mollit anim id est laborum.</p>
    <p style="margin-top:24px"><span class="btn">Read More</span></p>
  </div>
</section>

<!-- Services -->
<section>
  <div class="abs services"></div>
  <h2 class="abs section-title centered" style="top:1360px">What We Do<span class="title-bar"></span></h2>

  <div class="abs service-card" style="left:112px">
    <div class="service-photo" role="img" aria-label="Photo of a worker cleaning a glass facade" style="background:linear-gradient(160deg,#6e9fc7,#2f5d86)"></div>
    <div class="service-icon"><svg width="28" height="28" viewBox="0 0 28 28"><rect x="4" y="4" width="20" height="20" rx="2" fill="none" stroke="var(--orange)" stroke-width="2.5"/><path d="M14 4v20M4 14h20" stroke="var(--orange)" stroke-width="2.5"/></svg></div>
    <h3>Window &amp; Facade Cleaning</h3>
  </div>
  <div class="abs service-card" style="left:452px">
    <div class="service-photo" role="img" aria-label="Photo of a sanitised office hallway" style="background:linear-gradient(160deg,#e8dccb,#b59d7e)"></div>
    <div class="service-icon"><svg width="28" height="28" viewBox="0 0 28 28"><path d="M14 3l9 4v7c0 6-4 9-9 11-5-2-9-5-9-11V7z" fill="none" stroke="var(--red)" stroke-width="2.5"/><path d="M14 9v10M9 14h10" stroke="var(--red)" stroke-width="2.5"/></svg></div>
    <h3>Disinfection &amp; Sanitisation</h3>
  </div>
  <div class="abs service-card" style="left:792px">
    <div class="service-photo" role="img" aria-label="Photo of a carpet being vacuumed in an office" style="background:linear-gradient(160deg,#c8c1b6,#7d7366)"></div>
    <div class="service-icon"><svg width="28" height="28" viewBox="0 0 28 28"><circle cx="9" cy="20" r="4" fill="none" stroke="var(--orange)" stroke-width="2.5"/><path d="M13 20h10M9 16V5h6" fill="none" stroke="var(--orange)" stroke-width="2.5"/></svg></div>
    <h3>Floor &amp; Carpet Maintenance</h3>
  </div>
</section>

<!-- Why us -->
<section>
  <h2 class="abs section-title centered" style="top:1945px">Why Harbor Tidy Team?<span class="title-bar"></span></h2>
  <div class="abs why-frame"></div>
  <div class="abs why-emblem" role="img" aria-label="Brand emblem"></div>
  <div class="abs corner-icon" style="left:409px;top:2110px"><svg width="28" height="28" viewBox="0 0 28 28"><circle cx="14" cy="10" r="5" fill="#fff"/><path d="M5 25c1-6 5-8 9-8s8 2 9 8z" fill="#fff"/></svg></div>
  <div class="abs corner-icon" style="left:729px;top:2110px"><svg width="28" height="28" viewBox="0 0 28 28"><path d="M14 3l9 4v7c0 6-4 9-9 11-5-2-9-5-9-11V7z" fill="#fff"/><path d="M9 14l4 4 6-7" fill="none" stroke="var(--orange)" stroke-width="2.5"/></svg></div>
  <div class="abs corner-icon" style="left:409px;top:2310px"><svg width="28" height="28" viewBox="0 0 28 28"><path d="M6 22C6 10 14 5 24 5c0 10-5 18-17 18z" fill="#fff"/></svg></div>
  <div class="abs corner-icon" style="left:729px;top:2310px"><svg width="28" height="28" viewBox="0 0 28 28"><circle cx="14" cy="14" r="10" fill="none" stroke="#fff" stroke-width="2.5"/><path d="M14 8v6l4 3" fill="none" stroke="#fff" stroke-width="2.5"/></svg></div>

  <div class="abs feature" style="left:112px;top:2100px;text-align:right">
    <h4>Trained Certified Staff</h4>
    <p>Lorem ipsum dolor sit amet, consectetur adipiscing elit, sed do eiusmod tempor incididunt ut labore et dolore magna aliqua.</p>
  </div>
  <div class="abs feature" style="left:808px;top:2100px">
    <h4>Fully Insured</h4>
    <p>Lorem ipsum dolor sit amet, consectetur adipiscing elit, sed do eiusmod tempor incididunt ut labore et dolore magna aliqua.</p>
  </div>
  <div class="abs feature" style="left:112px;top:2300px;text-align:right">
    <h4>Eco-Friendly Products</h4>
    <p>Lorem ipsum dolor sit amet, consectetur adipiscing elit, sed do eiusmod tempor incididunt ut labore et dolore magna aliqua.</p>
  </div>
  <div class="abs feature" style="left:808px;top:2300px">
    <h4>Flexible Scheduling</h4>
    <p>Lorem ipsum dolor sit amet, consectetur adipiscing elit, sed do eiusmod tempor incididunt ut labore et dolore magna aliqua.</p>
  </div>
</section>

<!-- Commercial -->
<section>
  <div class="abs commercial"></div>
  <div class="abs commercial-copy">
    <h2 class="section-title">Cleaning Services for Commercial<span class="title-bar"></span></h2>
    <div class="stat">1000+ m² commercial space serviced weekly</div>
    <p>Lorem ipsum dolor sit amet, consectetur adipiscing elit, sed do eiusmod tempor incididunt ut labore et dolore magna aliqua.</p>
    <p>Ut enim ad minim veniam, quis nostrud exercitation ullamco laboris nisi ut aliquip ex ea commodo consequat. Duis aute irure dolor in reprehenderit eu fugiat nulla pariatur.</p>
    <p style="margin-top:26px"><span class="btn">Read More</span></p>
  </div>
  <div class="abs tile" style="left:624px;top:2640px;width:200px;height:170px;background:linear-gradient(160deg,#c9cfd6,#7c8794)" role="img" aria-label="Photo of an office floor being mopped"></div>
  <div class="abs tile" style="left:840px;top:2640px;width:248px;height:170px;background:linear-gradient(160deg,#e9c96a,#9a7c3a)" role="img" aria-label="Photo of a cleaner wearing yellow gloves wiping a surface"></div>
  <div class="abs tile" style="left:624px;top:2826px;width:248px;height:190px;background:linear-gradient(160deg,#d4dbe3,#8796a6)" role="img" aria-label="Photo of a bright commercial lobby"></div>
  <div class="abs tile" style="left:888px;top:2826px;width:200px;height:190px;background:linear-gradient(160deg,#c4d3e0,#5f7b94)" role="img" aria-label="Photo of a cleaner vacuuming an office"></div>
  <div class="abs collage-center" role="img" aria-label="Brand emblem"></div>
</section>

<!-- Partners -->
<section>
  <h2 class="abs section-title centered" style="top:3215px;color:var(--ink)">Our Partners<span class="title-bar" style="background:var(--ink)"></span></h2>
  <p class="abs partners-copy">Lorem ipsum dolor sit amet, consectetur adipiscing elit, sed do eiusmod tempor incididunt ut labore et dolore magna aliqua. Ut enim ad minim veniam, quis nostrud exercitation ullamco laboris nisi ut aliquip ex ea commodo consequat.</p>
  <div class="abs partner" style="left:-30px;background:#e6e6e6"></div>
  <div class="abs partner" style="left:150px;background:#2a9bd4"></div>
  <div class="abs partner" style="left:310px;background:#e4552c"></div>
  <div class="abs partner" style="left:470px;background:#2d3a6d"></div>
  <div class="abs partner" style="left:630px;background:#1f1f23"></div>
  <div class="abs partner" style="left:800px;background:#2d6fd1"></div>
  <div class="abs partner" style="left:1134px;background:#f0d9c8"></div>
</section>

<!-- Footer -->
<footer>
  <svg class="abs footer-wave" width="1200" height="140" viewBox="0 0 1200 140">
    <path d="M0 40 C300 120 520 -10 760 40 S1040 90 1200 20 L1200 140 L0 140Z" fill="var(--orange)"/>
    <path d="M0 70 C300 150 520 20 760 70 S1040 120 1200 50 L1200 140 L0 140Z" fill="var(--footer)"/>
  </svg>
  <div class="abs footer"></div>
  <div class="abs footer-brand"><span class="brand-dot"></span>Harbor Tidy Team</div>
  <div class="abs socials"><span></span><span></span><span></span><span></span></div>

  <div class="abs footer-col" style="left:480px">
    <h4>Quick Links</h4>
    <ul><li>Home</li><li>About Us</li><li>Services</li><li>Testimonials</li><li>Contact Us</li></ul>
  </div>
  <div class="abs footer-col" style="left:660px">
    <h4>Other Links</h4>
    <ul><li>FAQ</li><li>Terms of Use</li><li>Privacy Policy</li><li>Support Links</li><li>Conditions</li></ul>
  </div>
  <div class="abs footer-col" style="left:840px">
    <h4>Contact Us</h4>
    <div class="contact-row"><span class="contact-icon"><svg width="16" height="18" viewBox="0 0 16 20"><path d="M8 0a7 7 0 017 7c0 5-7 13-7 13S1 12 1 7a7 7 0 017-7z" fill="#fff"/><circle cx="8" cy="7" r="2.5" fill="var(--orange)"/></svg></span>Company Name, United States</div>
    <div class="contact-row"><span class="contact-icon"><svg width="16" height="12" viewBox="0 0 18 14"><rect x="1" y="1" width="16" height="12" rx="2" fill="none" stroke="#fff" stroke-width="2"/><path d="M1 2l8 6 8-6" fill="none" stroke="#fff" stroke-width="2"/></svg></span>info@companyname.in</div>
    <div class="contact-row"><span class="contact-icon"><svg width="16" height="16" viewBox="0 0 24 24"><path d="M6 2h4l2 5-3 2a12 12 0 006 6l2-3 5 2v4a2 2 0 01-2 2A18 18 0 014 4a2 2 0 012-2z" fill="#fff"/></svg></span>+1955 5555 5555</div>
  </div>
  <div class="abs copyright">Copyright@2025 Company Name All Rights Reserved</div>
</footer>

</body>
</html>
```